Podiatry Clinic needs an A0 poster design

we need an A0 poster design for our clinic frontage to include our logo and a feet theme. it is located either in a frame on a glass wall, or in a freestanding poster holder within a shopping centre.
Our clinic values are integrity, respect, excellence, happiness and fun.
We want to let people know that if your feet fail you, then the rest of you slows down very quickly, so get your feet checked immediately. we deal with kids feet, sporty feet, mature feet.

Target Market(s)

parents with kids

Industry/Entity Type

Medical

Requirements
Must have
• Bramblewick Health Logo
• www.bramblewickhealth.net
• 6172 0918
• easy to read from a distance
Nice to have
• fun, friendly, inviting, colourful, happy.
Should not have
• cartoon
• ugly
• sad
• not too much text
• no fanciful fonts

```html
<!DOCTYPE html>
<html lang="en">
<head>
<meta charset="utf-8">
<title>Bramblewick Health – Poster</title>
<link href="https://fonts.googleapis.com/css2?family=Arimo:wght@400;700&display=swap" rel="stylesheet">
<style>
  :root {
    --brand-blue: #0b4f9c;
    --brand-orange: #f07022;
    --sky-top: #d6f4fb;
    --sky-low: #b9e6f4;
    --grass-light: #6fb93a;
    --grass-dark: #2f7d1c;
    --paper: #ffffff;
  }
  * { margin: 0; padding: 0; box-sizing: border-box; }
  html, body { width: 849px; height: 1200px; overflow: hidden; background: var(--paper); }
  body { font-family: "Arimo", Arial, sans-serif; }
  .poster { position: relative; width: 849px; height: 1200px; background: var(--paper); }

  .hero {
    position: absolute; left: 0; top: 0; width: 849px; height: 718px;
    background: linear-gradient(180deg, var(--sky-top) 0%, var(--sky-low) 58%, var(--grass-light) 68%, var(--grass-dark) 100%);
  }
  .headline {
    position: absolute; left: 0; right: 0; top: 162px;
    text-align: center; color: var(--brand-blue);
    font-weight: 700; font-size: 67px; letter-spacing: -0.5px;
  }
  .tagline-pill {
    position: absolute; left: 18px; top: 602px; width: 814px; height: 78px;
    background: var(--brand-orange); border-radius: 39px;
    display: flex; align-items: center; justify-content: center;
    color: var(--paper); font-weight: 700; font-size: 42px; letter-spacing: -0.3px;
  }

  .brand-mark {
    position: absolute; left: 350px; top: 762px; width: 148px; height: 148px;
    border-radius: 50%; background: var(--brand-blue);
  }
  .brand-name {
    position: absolute; left: 0; right: 0; top: 922px; text-align: center;
    color: var(--brand-blue); font-weight: 400; font-size: 32px;
  }
  .slogan {
    position: absolute; left: 0; right: 0; top: 966px; text-align: center;
    color: var(--brand-orange); font-weight: 700; font-size: 27px;
  }
  .services {
    position: absolute; left: 40px; right: 40px; top: 1023px; text-align: center;
    color: var(--brand-blue); font-weight: 700; font-size: 14.5px; line-height: 19px;
  }
  .mission {
    position: absolute; left: 20px; right: 20px; top: 1082px; text-align: center;
    color: var(--brand-orange); font-weight: 700; font-size: 15px;
  }
  .contact {
    position: absolute; left: 0; right: 0; top: 1130px; text-align: center;
    color: var(--brand-blue); font-weight: 700; font-size: 35px;
  }
  .contact .dot { color: var(--brand-orange); }
</style>
</head>
<body>
<main class="poster">
  <div class="hero" role="img" aria-label="Photo of a row of children's bare feet as they lie on a grassy hill under a pale blue sky"></div>
  <h1 class="headline">High pace of life?</h1>
  <div class="tagline-pill">Don’t let your feet slow you down!</div>

  <div class="brand-mark" aria-hidden="true"></div>
  <div class="brand-name">Bramblewick Health</div>
  <div class="slogan">WE FIX FEET!</div>

  <p class="services">Bramblewick Health offers complete podiatry services for the entire family, from children, the elderly,<br>athletes and sports enthusiasts, to diabetics and high risk feet.</p>
  <p class="mission">Our Mission is to help you to enjoy a pain free, healthier and happier lifestyle from the feet up!</p>
  <p class="contact">www.bramblewickhealth.net <span class="dot">•</span> 6172 0918</p>
</main>
</body>
</html>
```